KAJU Freightways #ALLKAJU Business Cards & Letterhead

I am looking to business cards designed for our organization. We are currently undergoing a small re-branding that is taking place. Our organization is called KAJU Freightways and we are headquartered in Phoenix, AZ. We primarily provide transportation and logistics services to the Marlow Parcel Bureau who is our largest customer. I would like to see a design that incorporates name, title, contact info, website, and address (this will be different depending on the employee). I would also like to see some color on the business card using our logo colors or a variation. I would like our logo on the back of the business card with the website displayed. The final design should communicate that we are a next generation transportation operate that focuses on being driver-first, customer-centric, innovative, and sustainable.We would also like our #ALLKAJU catch phrase incorporated as well.

Target Market(s)

Transportation & Logistics

Industry/Entity Type

Trucking Company

Contact Information for Business Card

-First and Last Name
-Position Title
-Contact Phone
-Contact Email
-Physical Address

Font styles to use
Serif

Colors

Designer to choose colors to be used in the design.

Requirements
Must have
• -KAJU logo prominently displayed
• -#ALLKAJU catch phrase used
• -Some amount of color, design gradient, etc.
• -Logo on the back with website listed (https://www.kajufreightco.example)

```html
<!DOCTYPE html>
<html lang="en">
<head>
<meta charset="utf-8">
<title>KAJU Freightways Business Card</title>
<link href="https://fonts.googleapis.com/css2?family=Roboto+Slab:wght@400;500;700&display=swap" rel="stylesheet">
<style>
  :root {
    --ink: #0b3440;
    --green: #76b82a;
    --paper: #f3f3f2;
    --backdrop: #b9b9b9;
    --white: #ffffff;
  }
  * { margin: 0; padding: 0; box-sizing: border-box; }
  html, body {
    width: 1200px; height: 576px; overflow: hidden;
    background: var(--backdrop);
    font-family: "Roboto Slab", Georgia, serif;
  }
  .canvas { position: relative; width: 1200px; height: 576px; }
  .card {
    position: absolute;
    background: var(--paper);
    border-radius: 10px;
    overflow: hidden;
    box-shadow: 0 2px 6px rgba(0,0,0,0.18);
  }
  .card-back { left: 82px; top: 139px; width: 484px; height: 293px; }
  .card-front { left: 602px; top: 139px; width: 480px; height: 290px; }

  .brand-name {
    position: absolute;
    font-weight: 700;
    color: var(--ink);
    letter-spacing: 2px;
    line-height: 1;
  }
  .card-back .brand-name { left: 0; right: 0; top: 92px; text-align: center; font-size: 60px; }
  .catchphrase {
    position: absolute; left: 0; right: 0; top: 170px; text-align: center;
    font-size: 15px; font-weight: 500; letter-spacing: 3px; color: var(--green);
  }

  .back-website {
    position: absolute; left: 0; right: 0; top: 250px;
    display: flex; align-items: center; justify-content: center; gap: 20px;
    font-size: 12.5px; letter-spacing: 1.5px; color: var(--ink);
  }
  .back-website .rule { width: 40px; height: 3px; background: var(--green); border-radius: 2px; }
  .back-stripe { position: absolute; left: 0; right: 0; bottom: 0; height: 13px; display: flex; }
  .back-stripe .dark { flex: 1; background: var(--ink); }
  .back-stripe .light { flex: 1; background: var(--green); }

  .card-front .brand-name { left: 36px; top: 88px; font-size: 54px; }

  .front-wave { position: absolute; left: 0; top: 0; width: 480px; height: 290px; }

  .identity { position: absolute; right: 24px; top: 24px; text-align: right; }
  .person-name { font-size: 19px; font-weight: 700; color: var(--ink); }
  .person-title { font-size: 12.5px; color: var(--green); margin-top: 4px; }
  .address { margin-top: 16px; font-size: 12.5px; line-height: 18px; color: var(--ink); }

  .services {
    position: absolute; right: 24px; top: 178px; text-align: right;
    font-size: 12.5px; font-weight: 700; line-height: 16px; color: var(--white);
  }
  .contact-list {
    position: absolute; right: 24px; top: 222px; list-style: none;
    font-size: 11.5px; line-height: 18px; color: var(--white); text-align: right;
  }
  .contact-list li { display: flex; align-items: center; justify-content: flex-end; gap: 10px; }
  .contact-list svg { width: 11px; height: 11px; fill: var(--green); flex: none; }
</style>
</head>
<body>
<main class="canvas">

  <section class="card card-back" aria-label="Business card back">
    <span class="brand-name">KAJU</span>
    <p class="catchphrase">#ALLKAJU</p>
    <div class="back-website">
      <span class="rule"></span><span>www.kajufreightco.example</span><span class="rule"></span>
    </div>
    <div class="back-stripe"><span class="dark"></span><span class="light"></span></div>
  </section>

  <section class="card card-front" aria-label="Business card front">
    <svg class="front-wave" viewBox="0 0 480 290" aria-hidden="true">
      <path fill="var(--ink)" d="M0 262 C 90 300, 210 290, 300 222 C 360 176, 420 160, 480 160 L480 290 L0 290 Z"/>
      <path fill="var(--green)" d="M0 214 C 80 262, 210 258, 310 196 C 370 156, 430 136, 480 134 L480 146 C 430 148, 375 166, 318 204 C 220 270, 90 278, 0 236 Z"/>
      <path fill="var(--green)" d="M40 234 C 120 256, 220 254, 300 222 C 230 250, 130 256, 40 234 Z"/>
    </svg>

    <span class="brand-name">KAJU</span>

    <div class="identity">
      <p class="person-name">Dana Whitcombe</p>
      <p class="person-title">Chairman &amp; CEO</p>
      <p class="address">4410 North Cactus Ridge Road<br>Mesa, AZ 85201</p>
    </div>

    <p class="services">Transportation &amp;<br>Energy Services</p>

    <ul class="contact-list">
      <li>555-014-2290
        <svg viewBox="0 0 24 24"><path d="M6.6 10.8a15.1 15.1 0 0 0 6.6 6.6l2.2-2.2a1 1 0 0 1 1-.25 11.4 11.4 0 0 0 3.6.57 1 1 0 0 1 1 1V20a1 1 0 0 1-1 1A17 17 0 0 1 3 4a1 1 0 0 1 1-1h3.5a1 1 0 0 1 1 1c0 1.25.2 2.45.57 3.57a1 1 0 0 1-.25 1z"/></svg>
      </li>
      <li>www.kajufreightco.example
        <svg viewBox="0 0 24 24"><path d="M12 2a10 10 0 1 0 0 20 10 10 0 0 0 0-20zm6.9 6h-2.9a15.6 15.6 0 0 0-1.4-3.6A8 8 0 0 1 18.9 8zM12 4c.8 1.2 1.5 2.5 1.9 4h-3.8c.4-1.5 1.1-2.8 1.9-4zM4.3 14a8 8 0 0 1 0-4h3.4a16 16 0 0 0 0 4zm.8 2h2.9c.3 1.3.8 2.5 1.4 3.6A8 8 0 0 1 5.1 16zM8 8H5.1a8 8 0 0 1 4.3-3.6C8.8 5.5 8.4 6.7 8 8zm4 12c-.8-1.2-1.5-2.5-1.9-4h3.8c-.4 1.5-1.1 2.8-1.9 4zm2.3-6H9.7a14.7 14.7 0 0 1 0-4h4.6a14.7 14.7 0 0 1 0 4zm.3 5.6c.6-1.1 1.1-2.3 1.4-3.6h2.9a8 8 0 0 1-4.3 3.6zm1.7-5.6a16 16 0 0 0 0-4h3.4a8 8 0 0 1 0 4z"/></svg>
      </li>
      <li>dana@kajufreightco.example
        <svg viewBox="0 0 24 24"><path d="M2 5h20v14H2zm2 2v.5l8 5 8-5V7zm0 2.8V17h16V9.8l-8 5z"/></svg>
      </li>
    </ul>
  </section>

</main>
</body>
</html>
```